Vexlorn

I have a web site VEXLORN.com that is in serious need of a re-design. The site is mean't to be a portal for an app that I have called VEXLORN which you can see in the app store or googleplay. Take a look and see what you can do.
Updates

Project Deadline Extended
Reason: Still working with designers. The "look" is not quite there but a lot of progress has been made. RB

Industry/Entity Type

Store

```html
<!DOCTYPE html>
<html lang="en">
<head>
<meta charset="utf-8">
<title>Vexlorn – Sports Stats App</title>
<link href="https://fonts.googleapis.com/css2?family=Open+Sans:wght@400;600;700;800&family=Roboto+Condensed:wght@400;700&display=swap" rel="stylesheet">
<style>
  :root{
    --brand-blue:#1b6db3;
    --brand-green:#6cb33e;
    --ink:#3b4450;
    --muted:#6b7480;
    --nav-dark:#2d3a48;
    --hero-deep:#0b1f3c;
    --hero-mid:#1c4470;
    --field:#2f6a2a;
    --accent-orange:#f2a02a;
    --rule:#d8dde3;
    --white:#ffffff;
  }
  *{box-sizing:border-box;margin:0;padding:0}
  html,body{width:855px;height:1200px;overflow:hidden;background:var(--white)}
  body{font-family:"Open Sans",Arial,sans-serif;color:var(--ink);position:relative}

  /* Header */
  .site-header{height:80px;display:flex;align-items:center;justify-content:space-between;padding:0 40px 0 50px}
  .brand{display:flex;align-items:center;gap:10px}
  .brand-dot{width:26px;height:26px;border-radius:50%;background:var(--brand-green)}
  .brand-name{font-family:"Open Sans",sans-serif;font-weight:700;font-size:28px;color:var(--brand-blue)}
  .main-nav{display:flex;gap:4px;font-family:"Roboto Condensed",sans-serif;font-size:13px;font-weight:700}
  .main-nav a{color:var(--nav-dark);text-decoration:none;padding:10px 13px}
  .main-nav a.is-active{background:var(--nav-dark);color:var(--white)}

  /* Hero */
  .hero{position:relative;height:340px;overflow:hidden}
  .hero-photo{position:absolute;inset:0;background:linear-gradient(180deg,var(--hero-deep) 0%,var(--hero-mid) 55%,#2c5a4a 78%,var(--field) 100%)}
  .hero-copy{position:absolute;left:50px;top:26px;width:440px;color:var(--white)}
  .hero-title{font-size:15px;font-weight:600;line-height:1.35;text-transform:uppercase;letter-spacing:.3px}
  .hero-list{list-style:none;margin-top:14px;font-size:14px;line-height:1.65}
  .hero-list li{display:flex;align-items:center;gap:8px}
  .hero-list svg{flex:none}
  .hero-cta{margin-top:14px;font-size:19px;font-weight:600}
  .hero-cta strong{font-weight:800}
  .store-badges{display:flex;gap:12px;margin-top:10px}
  .store-badge{width:128px;height:40px;border-radius:7px;background:#111;border:1px solid #8a8f96}
  .hero-phone{position:absolute;right:95px;top:22px;width:150px;height:300px;border-radius:24px;background:linear-gradient(160deg,#f4f6f8,#cfd5dc)}

  /* Intro */
  .intro{padding:24px 90px 0;text-align:center}
  .intro-title{font-size:21px;font-weight:400;line-height:1.3;color:var(--brand-blue)}
  .intro-title strong{font-weight:700}
  .intro-text{margin-top:10px;font-size:11px;line-height:1.55;color:var(--muted)}

  /* Features */
  .features{display:flex;gap:40px;padding:16px 50px 0}
  .feature{flex:1}
  .feature-title{font-size:14px;font-weight:700;color:var(--brand-green);border-bottom:2px solid var(--brand-green);padding-bottom:4px;text-transform:uppercase}
  .feature-text{margin-top:7px;font-size:10.5px;line-height:1.5;color:var(--muted)}

  /* Fantasy band */
  .fantasy{position:absolute;left:0;top:700px;width:855px;height:295px;overflow:hidden}
  .fantasy-photo{position:absolute;inset:0;background:linear-gradient(90deg,#3c3a22 0%,#5a4a22 22%,#2a3e58 55%,#15304f 100%)}
  .fantasy-copy{position:absolute;left:460px;top:20px;width:360px;color:var(--white)}
  .fantasy-title{font-size:16px;font-weight:600}
  .fantasy-lead{font-size:10.5px;line-height:1.5;margin-top:5px;color:#d7e2ee}
  .fantasy-pitch{font-size:20px;font-weight:700;line-height:1.25;margin-top:16px}
  .fantasy-alert{font-size:11px;font-weight:800;color:var(--accent-orange);margin-top:14px;text-transform:uppercase;line-height:1.4}
  .fantasy-note{font-size:10.5px;line-height:1.5;color:#d7e2ee;margin-top:4px}

  /* On demand */
  .on-demand{position:absolute;left:0;top:995px;width:855px;height:113px}
  .on-demand-head{display:flex;align-items:center;gap:16px;padding:22px 230px 0 50px}
  .on-demand-head .rule{flex:1;height:1px;background:var(--rule)}
  .on-demand-title{font-size:20px;color:var(--brand-blue);font-weight:400}
  .on-demand-text{padding:8px 260px 0 70px;font-size:11px;line-height:1.55;color:var(--muted);text-align:center}
  .on-demand-photo{position:absolute;right:50px;top:8px;width:150px;height:100px;background:radial-gradient(ellipse at 60% 50%,#f1ede4 0%,#d9c8a4 55%,#ffffff 80%)}

  /* Footer */
  .site-footer{position:absolute;left:0;top:1108px;width:855px;height:92px;border-top:1px solid var(--rule);display:flex;align-items:center;justify-content:space-between;padding:0 50px}
  .social{display:flex;gap:8px}
  .social span{width:22px;height:22px;background:var(--brand-blue);border-radius:3px}
</style>
</head>
<body>
  <header class="site-header">
    <div class="brand"><span class="brand-dot"></span><span class="brand-name">Vexlorn</span></div>
    <nav class="main-nav">
      <a class="is-active" href="#">HOME</a><a href="#">ABOUT US</a><a href="#">BLOG</a><a href="#">FAQ</a><a href="#">CONTACT US</a>
    </nav>
  </header>

  <section class="hero">
    <div class="hero-photo" role="img" aria-label="Night stadium with floodlights over a green field"></div>
    <div class="hero-copy">
      <h1 class="hero-title">VEXLORN provides immediate access to the information you need:</h1>
      <ul class="hero-list">
        <li><svg width="12" height="12" viewBox="0 0 12 12"><path d="M1 6l3 3 7-7" fill="none" stroke="#6cb33e" stroke-width="2"/></svg>Team Statistics</li>
        <li><svg width="12" height="12" viewBox="0 0 12 12"><path d="M1 6l3 3 7-7" fill="none" stroke="#6cb33e" stroke-width="2"/></svg>Player Background</li>
        <li><svg width="12" height="12" viewBox="0 0 12 12"><path d="M1 6l3 3 7-7" fill="none" stroke="#6cb33e" stroke-width="2"/></svg>Live Scores</li>
        <li><svg width="12" height="12" viewBox="0 0 12 12"><path d="M1 6l3 3 7-7" fill="none" stroke="#6cb33e" stroke-width="2"/></svg>Schedules</li>
        <li><svg width="12" height="12" viewBox="0 0 12 12"><path d="M1 6l3 3 7-7" fill="none" stroke="#6cb33e" stroke-width="2"/></svg>Past Team and Player Performance</li>
      </ul>
      <p class="hero-cta">Download it now for <strong>FREE</strong></p>
      <div class="store-badges"><span class="store-badge"></span><span class="store-badge"></span></div>
    </div>
    <div class="hero-phone" role="img" aria-label="Smartphone showing the app's sign-in screen"></div>
  </section>

  <section class="intro">
    <h2 class="intro-title">Have You Ever Been <strong>Watching a Game</strong> and You Want to Know More <strong>about a Team</strong> or <strong>Player Stats?</strong></h2>
    <p class="intro-text">So, you're watching a game and want to know how another team is doing, or you want to check the stats of a team or player? VEXLORN puts all that information in your hands. It's easy to use, and you get the stats you want without getting distracted from the game.</p>
  </section>

  <section class="features">
    <article class="feature">
      <h3 class="feature-title">End the Hassle!</h3>
      <p class="feature-text">Why bother visiting different websites to find scores, player stats, schedules and past game performance? It is all on VEXLORN. Pick your sport, select your team and get the numbers you need.</p>
    </article>
    <article class="feature">
      <h3 class="feature-title">Get the Numbers!</h3>
      <p class="feature-text">Stats for pro football, college football, baseball, basketball, hockey and top-flight soccer. More leagues and sports are being added all the time.</p>
    </article>
  </section>

  <section class="fantasy">
    <div class="fantasy-photo" role="img" aria-label="Football players in action on the field under stadium lights"></div>
    <div class="fantasy-copy">
      <h3 class="fantasy-title">On The Go and You Need To Know</h3>
      <p class="fantasy-lead">Use VEXLORN on your phone to follow the live scores and look up a team's or player's history in a few quick taps.</p>
      <p class="fantasy-pitch">Perfect for the fantasy game player. Get team and player stats from previous games this season</p>
      <p class="fantasy-alert">No need to go through layers of stats from other sport sites.</p>
      <p class="fantasy-note">VEXLORN gives you the numbers right away, so you can set your lineup with confidence.</p>
    </div>
  </section>

  <section class="on-demand">
    <div class="on-demand-head"><span class="rule"></span><h2 class="on-demand-title">Sport Stats on Demand</h2><span class="rule"></span></div>
    <p class="on-demand-text">Forget about relying on sportscasters or the ticker at the bottom of your screen for the scores you want. Just select your league, go to your team, and get the score. All in a matter of seconds.</p>
    <div class="on-demand-photo" role="img" aria-label="Baseball bat and ball"></div>
  </section>

  <footer class="site-footer">
    <div class="brand"><span class="brand-dot"></span><span class="brand-name">Vexlorn</span></div>
    <div class="social"><span></span><span></span><span></span></div>
  </footer>
</body>
</html>
```